Postcard Design - Thanksgiving Card - Norvale Thermal Coils

Here are just a few of the heating and cooling products we offer:

• Steam Coils • Convector Coils
• Hot Water Coils • Re-Heat Coils
• Chilled Water Coils • Tube Bundles
• Direct Expansion (Evaporator) Coils • Shell & Tube Heat Exchangers
• Condensing Coils • Custom Coils to end user spec.’s

ENGINEERING - We can duplicate any existing equipment, even equipment that has been obsolete for years. Norvale Thermal personnel will come directly to your job site and match-up dimensions, materials, and performance - all free of charge. We can build from copper, aluminum, cupro-nickel, brass, and more. Heat exchangers and tube bundles can be replaced & warranted as new with great savings; this includes Hadley & Prowse, Wexford-Lanning, Zuno, and others. We also make engineering recommendations and suggestions regarding the correct ways to replace equipment or methods of increasing the life expectancy of equipment. We will help solve your HVAC problems, not duplicate them.

Hvac

```html
<!DOCTYPE html>
<html lang="en">
<head>
<meta charset="utf-8">
<title>Norvale Thermal Coils – Thanksgiving Postcard</title>
<link rel="stylesheet" href="https://fonts.googleapis.com/css2?family=Montserrat:wght@400;500;700&family=Roboto+Condensed:ital,wght@1,300&family=Great+Vibes&family=Pinyon+Script&display=swap">
<style>
  :root {
    --stage: #000000;
    --brown: #5b2a1c;
    --brown-deep: #3f1d12;
    --ink: #4a3a33;
    --ink-soft: #6b625d;
    --panel: rgba(236, 236, 238, 0.93);
    --copper-hi: #e9b3a8;
    --copper: #a8685c;
    --copper-dark: #2a1a18;
    --cream: #fbf5ec;
    --leaf: #e8c7a2;
    --white: #ffffff;
  }
  * { box-sizing: border-box; margin: 0; padding: 0; }
  html, body { width: 783px; height: 1200px; overflow: hidden; background: var(--stage); }
  .canvas { position: relative; width: 783px; height: 1200px; }

  .postcard { position: absolute; left: 46px; width: 691px; height: 535px; overflow: hidden; }
  .postcard--front { top: 57px; background: var(--copper-dark); }
  .postcard--back { top: 618px; background: var(--cream); }

  /* front */
  .front__backdrop { position: absolute; inset: 0;
    background: linear-gradient(90deg, #3a2420 0%, #5d3a34 50%, #241816 100%); }
  .front__photo { position: absolute; left: 393px; top: 0; width: 298px; height: 535px;
    background:
      repeating-linear-gradient(180deg, rgba(0,0,0,0) 0 22px, rgba(20,10,10,0.55) 22px 54px),
      linear-gradient(90deg, var(--copper) 0%, var(--copper-hi) 45%, var(--copper) 100%); }
  .front__panel { position: absolute; left: 45px; top: 0; width: 348px; height: 535px;
    background: var(--panel); text-align: center; }
  .brand-name { position: absolute; left: 0; right: 0; top: 62px;
    font: 700 19px/1.2 "Montserrat", sans-serif; color: var(--brown-deep); letter-spacing: .02em; }
  .brand-mark { display: inline-block; width: 12px; height: 12px; background: var(--brown-deep);
    margin-right: 8px; vertical-align: 1px; }
  .greeting-quote { position: absolute; left: 36px; right: 28px; top: 150px;
    font: italic 300 17px/26px "Roboto Condensed", sans-serif; color: var(--ink-soft); }
  .signatures { position: absolute; left: 62px; right: 50px; top: 308px; display: flex;
    justify-content: space-between; font: 34px/1 "Pinyon Script", cursive; color: var(--brown); }
  .product-list { position: absolute; left: 0; right: 0; top: 368px; list-style: none;
    font: 400 13px/16.5px "Montserrat", sans-serif; color: var(--ink); }
  .contact-band { position: absolute; left: 0; top: 481px; width: 691px; height: 35px;
    background: var(--brown); color: var(--white); display: flex; align-items: center;
    justify-content: center; gap: 6px; font: 400 14.5px/1 "Montserrat", sans-serif; }
  .contact-band strong { font-weight: 700; }

  /* back */
  .back__leaf { position: absolute; left: 0; top: 0; width: 430px; height: 535px;
    background: radial-gradient(ellipse at 35% 40%, var(--leaf) 0%, rgba(232,199,162,.6) 45%, rgba(251,245,236,0) 75%); }
  .back__glow { position: absolute; right: 0; top: 0; width: 420px; height: 535px;
    background: radial-gradient(ellipse at 70% 10%, rgba(240,214,150,.55) 0%, rgba(251,245,236,0) 60%); }
  .return-address { position: absolute; left: 60px; width: 214px; top: 50px; text-align: center;
    font: normal 400 13.5px/17px "Montserrat", sans-serif; color: var(--ink); }
  .leaf-sprig { position: absolute; left: 150px; top: 128px; width: 90px; height: 58px;
    border-radius: 50%; background: radial-gradient(ellipse, #d8a866 0%, rgba(216,168,102,0) 70%); }
  .holiday-greeting { position: absolute; left: 48px; top: 186px; width: 300px;
    font: 400 62px/54px "Great Vibes", cursive; color: var(--brown-deep); }
  .holiday-greeting span { display: block; }
  .holiday-greeting span:first-child { padding-left: 60px; }
  .back__brand { position: absolute; left: 48px; width: 242px; top: 362px; text-align: center;
    font: 700 18px/1.2 "Montserrat", sans-serif; color: var(--brown-deep); white-space: nowrap; }
  .service-tag { position: absolute; left: 78px; width: 181px; top: 437px; height: 21px;
    background: var(--brown); color: var(--white); text-align: center;
    font: 700 14px/21px "Montserrat", sans-serif; }
  .back__phone { position: absolute; left: 48px; width: 242px; top: 462px; text-align: center;
    font: 700 21px/1 "Montserrat", sans-serif; color: var(--brown-deep); }
  .back__email { position: absolute; left: 48px; width: 242px; top: 488px; text-align: center;
    font: 400 13px/1 "Montserrat", sans-serif; color: var(--ink); }
</style>
</head>
<body>
<main class="canvas">
  <section class="postcard postcard--front">
    <div class="front__backdrop"></div>
    <div class="front__photo" role="img" aria-label="Close-up photograph of copper coil tube bends"></div>
    <div class="front__panel">
      <div class="brand-name"><span class="brand-mark"></span>Norvale Thermal<br>Coils</div>
      <p class="greeting-quote">“It is the time of Year for remembering everything that makes us grateful. That is why we want to express our appreciation for your confidence in our firm to assist you on your jobsite or at your facility to solve a coil or heat exchanger problem.”</p>
      <div class="signatures"><span>Dale</span><span>Reed</span></div>
      <ul class="product-list">
        <li>• Steam Coils • Hot Water Coils</li>
        <li>• Chilled Water Coils • Condensing Coils</li>
        <li>• Direct Expansion (Evaporator) Coils</li>
        <li>• Convector Coils • Re-Heat Coils</li>
        <li>• Tube Bundles • Shell &amp; Tube Heat Exchangers</li>
        <li>• Custom Coils to end user spec.’s</li>
      </ul>
    </div>
    <div class="contact-band">
      <span>Serving all of Michigan</span><span>|</span><strong>888-555-0147</strong><span>|</span><span>coilpro@northmail.net</span>
    </div>
  </section>

  <section class="postcard postcard--back">
    <div class="back__leaf" role="img" aria-label="Soft photograph of an autumn maple leaf"></div>
    <div class="back__glow"></div>
    <address class="return-address">Dale Morrow &amp; Reed Halvers<br>P.O. Box 718<br>Lakemont, MI 48099</address>
    <div class="leaf-sprig" role="img" aria-label="Small illustration of autumn leaves"></div>
    <h1 class="holiday-greeting"><span>Happy</span><span>Thanksgiving!</span></h1>
    <div class="back__brand"><span class="brand-mark"></span>Norvale Thermal Coils</div>
    <div class="service-tag">Serving all of Michigan</div>
    <div class="back__phone">888-555-0147</div>
    <div class="back__email">coilpro@northmail.net</div>
  </section>
</main>
</body>
</html>
```